Coastline Premier Retreats Business Card Design

Design a business card for Coastline Premier Retreats. Look at the website for colors and reference. Card should have logo, name, title, office number, mobile number, email, URL and a tagline like, "Luxury Hotel & Resort Email Marketing" (This might change).

https://www.coastlinepremierretreats.example

The rest I will leave up to your imagination.

Contact Information for Business Card

Logo, name, title, office number, mobile number, email, URL and a tagline like, "Luxury Hotel & Resort Email Marketing" (This might change).

```html
<!DOCTYPE html>
<html lang="en">
<head>
<meta charset="utf-8">
<title>Coastline Premier Retreats – Business Card</title>
<link rel="stylesheet" href="https://fonts.googleapis.com/css2?family=Open+Sans:wght@400;600;700&display=swap">
<style>
  :root {
    --bg: #232323;
    --card: #202024;
    --orange: #f47a20;
    --white: #ffffff;
    --line: #e8e8e8;
  }
  * { box-sizing: border-box; margin: 0; padding: 0; }
  html, body { width: 1200px; height: 780px; overflow: hidden; background: var(--bg); }
  body { font-family: "Open Sans", Arial, sans-serif; }
  .canvas {
    width: 1200px; height: 780px;
    display: flex; align-items: center; justify-content: center; gap: 40px;
  }
  .card {
    position: relative;
    width: 540px; height: 309px;
    background: var(--card);
    border-bottom: 5px solid var(--orange);
    box-shadow: 0 14px 30px rgba(0,0,0,0.55);
    overflow: hidden;
  }
  /* Front */
  .card--front { display: flex; align-items: center; justify-content: center; }
  .brand { display: flex; align-items: center; gap: 14px; }
  .brand__mark { width: 14px; height: 14px; background: var(--orange); }
  .brand__name {
    color: var(--white); font-weight: 700; font-size: 26px;
    letter-spacing: 0.04em; text-transform: uppercase;
  }
  /* Back */
  .identity { position: absolute; left: 38px; top: 118px; width: 210px; text-align: right; }
  .identity__name { font-size: 24px; font-weight: 700; line-height: 1.1; white-space: nowrap; }
  .identity__first { color: var(--orange); }
  .identity__last { color: var(--white); }
  .identity__title { color: var(--white); font-size: 13px; margin-top: 4px; }
  .divider {
    position: absolute; left: 264px; top: 92px;
    width: 2px; height: 100px; background: var(--line);
  }
  .contacts { position: absolute; left: 282px; top: 96px; list-style: none; }
  .contacts__item {
    display: flex; align-items: center; gap: 8px;
    color: var(--white); font-size: 10.5px; line-height: 23px; white-space: nowrap;
  }
  .contacts__icon { width: 12px; height: 12px; flex: none; }
  .tagline {
    position: absolute; left: 0; right: 0; bottom: 30px;
    text-align: center; color: var(--orange); font-size: 13px; letter-spacing: 0.02em;
  }
</style>
</head>
<body>
<main class="canvas">
  <section class="card card--front" aria-label="Card front">
    <div class="brand">
      <span class="brand__mark"></span>
      <span class="brand__name">Coastline Premier Retreats</span>
    </div>
  </section>

  <section class="card card--back" aria-label="Card back">
    <div class="identity">
      <p class="identity__name"><span class="identity__first">Marta</span> <span class="identity__last">Kovalenko</span></p>
      <p class="identity__title">Managing Director</p>
    </div>
    <div class="divider"></div>
    <ul class="contacts">
      <li class="contacts__item">
        <svg class="contacts__icon" viewBox="0 0 24 24" fill="var(--orange)"><path d="M6.6 10.8a15 15 0 0 0 6.6 6.6l2.2-2.2a1 1 0 0 1 1-.25 11.4 11.4 0 0 0 3.6.6 1 1 0 0 1 1 1V20a1 1 0 0 1-1 1A17 17 0 0 1 3 4a1 1 0 0 1 1-1h3.5a1 1 0 0 1 1 1c0 1.25.2 2.45.6 3.6a1 1 0 0 1-.25 1z"/></svg>
        <span>(555) 014-2758</span>
      </li>
      <li class="contacts__item">
        <svg class="contacts__icon" viewBox="0 0 24 24" fill="none" stroke="var(--orange)" stroke-width="2"><rect x="6" y="2" width="12" height="20" rx="2"/><line x1="11" y1="18" x2="13" y2="18"/></svg>
        <span>(555) 014-7777</span>
      </li>
      <li class="contacts__item">
        <svg class="contacts__icon" viewBox="0 0 24 24" fill="none" stroke="var(--orange)" stroke-width="2"><circle cx="12" cy="12" r="10"/><path d="M2 12h20M12 2a15 15 0 0 1 0 20M12 2a15 15 0 0 0 0 20"/></svg>
        <span>www.coastlinepremierretreats.example</span>
      </li>
      <li class="contacts__item">
        <svg class="contacts__icon" viewBox="0 0 24 24" fill="none" stroke="var(--orange)" stroke-width="2"><rect x="2" y="5" width="20" height="14" rx="1"/><path d="M2 6l10 7 10-7"/></svg>
        <span>info@coastlinepremierretreats.example</span>
      </li>
    </ul>
    <p class="tagline">Luxury Hotel &amp; Resort Email Marketing</p>
  </section>
</main>
</body>
</html>
```